Corporate Design für Steuerkanzlei
Zielgruppe
Wir sind eine Steuerkanzlei im (ländlichen) Neustadt an der Donau, die seit über 30 Jahren von Herrn Konrad (Vater) Wehrle geführt wird. Mit Einstieg durch Herrn Florian (Sohn) Wehrle haben wir die Wehrle Steuerberatungsgellschaft mbH gegründet und suchen deshalb ein neues Kanzleilogo / Geschäftspapiere. Wir betreuen/beraten kleine Unternehmen und Privatpersonen aus der Region und haben derzeitig 14 Angestellte.
Aufgabenstellung
Das Design sollte in erster Linie seriös und nicht verspielt wirken. Einer vertrauensvollen Steuerberaterungskanzlei entsprechend. Dennoch sind wir auch für eine moderne Gestaltung offen.

```html
<!DOCTYPE html>
<html lang="de">
<head>
<meta charset="utf-8">
<title>Wehrle Steuerberatungsgesellschaft mbH – Geschäftsausstattung</title>
<link rel="stylesheet" href="https://fonts.googleapis.com/css2?family=Source+Sans+3:ital,wght@0,400;0,600;1,400&display=swap">
<style>
  :root {
    --bg: #e6e6e6;
    --paper: #ffffff;
    --brand: #0b9cbd;
    --text: #3c3c3c;
    --tagline: #565656;
    --shadow: rgba(0,0,0,0.18);
  }
  * { margin: 0; padding: 0; box-sizing: border-box; }
  html, body { width: 1200px; height: 930px; overflow: hidden; }
  body {
    background: var(--bg);
    font-family: "Source Sans 3", "Source Sans Pro", Arial, sans-serif;
    color: var(--text);
    position: relative;
  }
  .wordmark {
    position: absolute;
    font-weight: 600;
    color: var(--brand);
    line-height: 1;
    letter-spacing: -0.01em;
    white-space: nowrap;
  }
  .tagline {
    position: absolute;
    color: var(--tagline);
    font-weight: 600;
    line-height: 1;
    white-space: nowrap;
  }
  /* Large brand presentation */
  .hero .wordmark { left: 54px; top: 30px; font-size: 116px; }
  .hero .tagline { left: 250px; top: 131px; font-size: 23px; }

  .sheet {
    position: absolute;
    background: var(--paper);
    box-shadow: 0 1px 2px var(--shadow);
  }
  /* Letterhead */
  .letterhead { left: 372px; top: 215px; width: 377px; height: 533px; }
  .letterhead .wordmark { left: 28px; top: 20px; font-size: 33px; }
  .letterhead .tagline { left: 90px; top: 56px; font-size: 7px; color: var(--text); }
  .letterhead .company-info {
    position: absolute; left: 250px; top: 391px;
    font-size: 5.8px; line-height: 7.6px;
    white-space: nowrap;
  }
  .company-info p + p { margin-top: 5px; }
  .company-info strong { font-weight: 600; font-size: 6.4px; }

  /* Business card front */
  .card-front { left: 824px; top: 360px; width: 185px; height: 113px; }
  .card-front .wordmark { left: 13px; top: 62px; font-size: 30px; }
  .card-front .tagline { left: 72px; top: 96px; font-size: 6.6px; color: var(--text); }

  /* Business card back */
  .card-back { left: 824px; top: 530px; width: 185px; height: 113px; }
  .card-back .wordmark { left: 11px; top: 9px; font-size: 24px; }
  .card-back .person { position: absolute; right: 10px; top: 40px; text-align: right; }
  .person .name { font-size: 9px; font-weight: 600; line-height: 10px; }
  .person .role { font-size: 7px; font-style: italic; line-height: 9px; }
  .card-back .contact {
    position: absolute; left: 10px; top: 65px;
    font-size: 5.8px; line-height: 7.8px;
    white-space: nowrap;
  }
</style>
</head>
<body>
  <section class="hero">
    <div class="wordmark">Wehrle</div>
    <div class="tagline">Steuerberatungsgesellschaft mbH</div>
  </section>

  <section class="sheet letterhead">
    <div class="wordmark">Wehrle</div>
    <div class="tagline">Steuerberatungsgesellschaft mbH</div>
    <div class="company-info">
      <p><strong>Wehrle<br>Steuerberatungsgesellschaft mbh</strong><br>Lindenweg 16<br>84107 Auenfeld</p>
      <p>Telefon: 0 87 12 / 61 480-0<br>Telefax: 0 87 12 / 61 480-29<br>Mail: info@stb-wehrle.de</p>
      <p>St.-Nr.: 204/318/55021<br>UMST.-Nr.: DE 481305772<br>HRB 40712 Amtsgericht Auenfeld</p>
      <p>Bankverbindung<br>IBAN: DE41 640 217 553<br>BIC: AUFEDEX1XXX</p>
    </div>
  </section>

  <section class="sheet card-front">
    <div class="wordmark">Wehrle</div>
    <div class="tagline">Steuerberatungsgesellschaft mbH</div>
  </section>

  <section class="sheet card-back">
    <div class="wordmark">Wehrle</div>
    <div class="person">
      <div class="name">Florian Wehrle</div>
      <div class="role">Steuerberater</div>
    </div>
    <div class="contact">
      Lindenweg 16<br>84107 Auenfeld<br>Telefon: 0 87 12 / 61 480-0<br>Telefax: 0 87 12 / 61 480-29<br>Mail: info@stb-wehrle.de
    </div>
  </section>
</body>
</html>
```